Business cards and stationary design

We just completed the design of our new logo and we need to print new business cards and letterhead for our nonprofit. We are looking for a fresh new design that shows off our new logo. On letterhead, we must have a column on the right or left to include our Board of Directors (up to 45 names) (see attachment)

Industry/Entity Type

Non-Profit

Contact Information for Business Card

Standard business card with name, title, Company name, mailing address phone numbers, email address and website. Tagline on back "Opening doors to steady ground"

Font styles to use
Sans Serif

Requirements
Must have
• include pertinent information above
• new logo
• fonts compatible with logo
• should use logo colors only
Nice to have
• tag lines

```html
<!DOCTYPE html>
<html lang="en">
<head>
<meta charset="utf-8">
<title>Harbor Shelter Alliance — Business Card</title>
<link rel="stylesheet" href="https://fonts.googleapis.com/css2?family=Michroma&family=Open+Sans:wght@400;600&family=Crimson+Text&display=swap">
<style>
  :root {
    --teal: #1b7f9a;
    --red: #e8232a;
    --orange-deep: #ec2a24;
    --orange-bright: #f9a227;
    --ink: #4a4a4a;
    --paper: #ffffff;
    --backdrop: #ecebe8;
  }
  * { box-sizing: border-box; margin: 0; padding: 0; }
  html, body { width: 1200px; height: 1200px; overflow: hidden; }
  body {
    background: var(--backdrop);
    display: flex;
    flex-direction: column;
    align-items: center;
    justify-content: center;
    gap: 60px;
  }
  .card {
    width: 900px;
    height: 514px;
    position: relative;
    box-shadow: 0 6px 18px rgba(0,0,0,0.12);
  }

  /* Front */
  .card-front {
    background: var(--paper);
    display: flex;
    align-items: center;
    padding: 0 60px;
  }
  .brand {
    width: 290px;
    flex: none;
    display: flex;
    align-items: center;
    gap: 14px;
  }
  .brand-mark {
    width: 22px; height: 22px;
    background: var(--teal);
    flex: none;
  }
  .brand-name {
    font-family: "Michroma", sans-serif;
    font-size: 20px;
    line-height: 1.35;
    letter-spacing: 1px;
    color: var(--teal);
    text-transform: uppercase;
  }
  .person { margin-left: 30px; }
  .person-name {
    font-family: "Michroma", sans-serif;
    font-size: 26px;
    font-weight: 400;
    letter-spacing: 2px;
    white-space: nowrap;
    color: var(--red);
    text-transform: uppercase;
  }
  .person-title {
    font-family: "Open Sans", sans-serif;
    font-size: 16px;
    color: var(--ink);
    margin-top: 6px;
  }
  .contact {
    margin-top: 40px;
    font-family: "Open Sans", sans-serif;
    font-size: 16px;
    border-collapse: collapse;
  }
  .contact td { padding: 3px 0; white-space: nowrap; }
  .contact-label { color: var(--red); width: 80px; }
  .contact-sep { color: var(--red); width: 24px; }
  .contact-value { color: var(--ink); }

  /* Back */
  .card-back {
    background: linear-gradient(30deg, var(--orange-deep) 0%, #f06a24 50%, var(--orange-bright) 100%);
    display: flex;
    flex-direction: column;
    align-items: center;
    justify-content: center;
    color: var(--paper);
  }
  .back-brand {
    display: flex;
    align-items: center;
    gap: 18px;
  }
  .back-brand .brand-mark { background: var(--paper); width: 28px; height: 28px; }
  .back-brand .brand-name { color: var(--paper); font-size: 34px; white-space: nowrap; }
  .tagline {
    font-family: "Crimson Text", serif;
    font-size: 36px;
    margin-top: 26px;
  }
</style>
</head>
<body>
  <section class="card card-front">
    <div class="brand">
      <span class="brand-mark"></span>
      <span class="brand-name">Harbor Shelter<br>Alliance</span>
    </div>
    <div class="person">
      <h1 class="person-name">Daniel Marlowe</h1>
      <p class="person-title">Chairman</p>
      <table class="contact">
        <tr><td class="contact-label">Address</td><td class="contact-sep">:</td><td class="contact-value">P.O Box 5820, Riverton, Texas 75031</td></tr>
        <tr><td class="contact-label">Tel</td><td class="contact-sep">:</td><td class="contact-value">555.010.4821</td></tr>
        <tr><td class="contact-label">Email</td><td class="contact-sep">:</td><td class="contact-value">daniel@hsalliance.org</td></tr>
        <tr><td class="contact-label">Web</td><td class="contact-sep">:</td><td class="contact-value">www.hsalliance.org</td></tr>
      </table>
    </div>
  </section>

  <section class="card card-back">
    <div class="back-brand">
      <span class="brand-mark"></span>
      <span class="brand-name">Harbor Shelter Alliance</span>
    </div>
    <p class="tagline">Opening doors to steady ground</p>
  </section>
</body>
</html>
```